Timber Crest Construction Needs business card

Hey we are in need of business card designs. I have upload our logo as a guideline, but free feel to run with it or come up with something unique.
Pls have fun with it and be creative. the name says it all!
i will give some directions after i see a few entries..
Updates
Logo source file has been uploaded..
Hey because of the logo is so colourful already.
Can we have a few submissions with less colour.
Also we are looking for clever/hidden/descriptive business card.

```html
<!DOCTYPE html>
<html lang="en">
<head>
<meta charset="utf-8">
<title>Timber Crest Construction – Business Card</title>
<link href="https://fonts.googleapis.com/css2?family=Montserrat:wght@500;700&family=Questrial&display=swap" rel="stylesheet">
<style>
  :root {
    --stage: #1f7d0a;
    --ink: #000000;
    --charcoal: #1a1a1a;
    --paper: #ffffff;
    --brand-grey: #7b7b7d;
    --accent-red: #e3171f;
    --accent-yellow: #fcc30b;
    --accent-blue: #0a7ac8;
    --accent-green: #00883e;
    --text-dark: #222222;
  }
  * { margin: 0; padding: 0; box-sizing: border-box; }
  html, body { width: 1200px; height: 1200px; overflow: hidden; }
  body {
    background: var(--stage);
    position: relative;
    font-family: "Questrial", "Century Gothic", sans-serif;
  }
  .card {
    position: absolute;
    left: 212px;
    width: 800px;
    height: 445px;
    overflow: hidden;
  }
  .card--front { top: 130px; background: var(--ink); }
  .card--back { top: 641px; background: var(--paper); }

  .block-pattern {
    position: absolute;
    left: 8px; top: 0;
    width: 320px; height: 445px;
    background: linear-gradient(160deg, #0a5d9a 0%, #3a3a3c 30%, #b5161c 55%, #c99a0a 75%, #006b31 100%);
    opacity: 0.85;
  }

  .wordmark {
    position: absolute;
    display: flex;
    align-items: center;
    gap: 12px;
    font-family: "Montserrat", sans-serif;
    font-weight: 700;
    color: var(--brand-grey);
    text-transform: uppercase;
    line-height: 1.05;
  }
  .wordmark__square {
    width: 34px; height: 34px;
    background: var(--brand-grey);
    flex: none;
  }
  .wordmark__name { font-size: 30px; letter-spacing: -0.5px; }
  .wordmark__name small { display: block; font-size: 14px; letter-spacing: 1px; text-align: center; }
  .card--front .wordmark { left: 364px; top: 248px; }
  .card--back .wordmark { left: 42px; top: 200px; }

  .contact { position: absolute; left: 436px; top: 76px; color: var(--text-dark); }
  .contact__name {
    font-family: "Montserrat", sans-serif;
    font-weight: 700;
    font-size: 16px;
    letter-spacing: 3.5px;
    text-transform: uppercase;
  }
  .contact__role {
    margin-top: 6px;
    font-size: 14px;
    letter-spacing: 2.6px;
    color: var(--accent-red);
    text-transform: uppercase;
  }
  .contact__address {
    margin-top: 42px;
    font-size: 14px;
    line-height: 21px;
    letter-spacing: 2.6px;
    text-transform: uppercase;
    font-style: normal;
  }
  .contact__list { list-style: none; margin-top: 38px; }
  .contact__item {
    display: flex;
    align-items: center;
    height: 25.3px;
    font-size: 14px;
    letter-spacing: 2.4px;
  }
  .contact__icon { width: 16px; height: 16px; margin-right: 21px; flex: none; }

  .wave { position: absolute; left: 0; top: 0; width: 800px; height: 445px; }
</style>
</head>
<body>
  <section class="card card--front" aria-label="Business card front">
    <div class="block-pattern" role="img" aria-label="Large decorative pattern of coloured building blocks"></div>
    <div class="wordmark">
      <span class="wordmark__square"></span>
      <span class="wordmark__name">Timber Crest<small>Construction</small></span>
    </div>
  </section>

  <section class="card card--back" aria-label="Business card back">
    <div class="wordmark">
      <span class="wordmark__square"></span>
      <span class="wordmark__name">Timber Crest<small>Construction</small></span>
    </div>

    <div class="contact">
      <p class="contact__name">Marta Kovel</p>
      <p class="contact__role">Director</p>
      <address class="contact__address">Unit 3, 212-216 Harbour<br>Street Ashfield North</address>
      <ul class="contact__list">
        <li class="contact__item">
          <svg class="contact__icon" viewBox="0 0 16 16" aria-label="Phone"><path d="M1 5 Q8 0 15 5 L13 7 L11 5 H5 L3 7 Z M4 8 H12 L14 14 H2 Z" fill="var(--accent-red)"/><circle cx="8" cy="11" r="1.8" fill="#fff"/></svg>
          9718 2054
        </li>
        <li class="contact__item">
          <svg class="contact__icon" viewBox="0 0 16 16" aria-label="Fax"><rect x="4" y="1" width="8" height="4" fill="none" stroke="var(--accent-red)" stroke-width="1.5"/><rect x="1" y="5" width="14" height="6" rx="1" fill="none" stroke="var(--accent-red)" stroke-width="1.5"/><rect x="4" y="9" width="8" height="6" fill="#fff" stroke="var(--accent-red)" stroke-width="1.5"/></svg>
          9718 2066
        </li>
        <li class="contact__item">
          <svg class="contact__icon" viewBox="0 0 16 16" aria-label="Email"><rect x="1" y="3" width="14" height="10" fill="none" stroke="var(--accent-red)" stroke-width="1.5"/><path d="M1 3 L8 9 L15 3" fill="none" stroke="var(--accent-red)" stroke-width="1.5"/></svg>
          marta@timbercrestbuild.com
        </li>
        <li class="contact__item">
          <svg class="contact__icon" viewBox="0 0 16 16" aria-label="Website"><circle cx="8" cy="8" r="6.5" fill="none" stroke="var(--accent-red)" stroke-width="1.5"/><path d="M1.5 8 H14.5 M8 1.5 Q4 8 8 14.5 M8 1.5 Q12 8 8 14.5" fill="none" stroke="var(--accent-red)" stroke-width="1.2"/></svg>
          www.timbercrestbuild.com
        </li>
      </ul>
    </div>

    <svg class="wave" viewBox="0 0 800 445" aria-hidden="true">
      <path d="M0 356 C150 340 300 368 460 404 L450 410 C300 380 150 355 0 372 Z" fill="var(--accent-yellow)"/>
      <path d="M420 400 C560 432 660 428 800 338 L800 355 C650 430 560 430 450 410 Z" fill="var(--accent-red)"/>
      <path d="M0 372 C150 355 300 380 450 410 C560 430 650 430 800 355 L800 445 L0 445 Z" fill="var(--charcoal)"/>
    </svg>
  </section>
</body>
</html>
```